Personal letterhead and stationary

I am looking for someone to design letterhead and stationary set for my personal use. I want something simple and timeless with a little bit of color. I like photography, computers and writing.

```html
<!DOCTYPE html>
<html lang="en">
<head>
<meta charset="utf-8">
<title>Dominic Lee Harlow — Letterhead</title>
<link href="https://fonts.googleapis.com/css2?family=Lato:wght@300;400&family=Crimson+Text:wght@400&display=swap" rel="stylesheet">
<style>
  :root {
    --ink: #111111;
    --accent-blue: #5aaee0;
    --page: #ffffff;
    --sheet: #fcfcfb;
    --sheet-border: #bdbdbd;
  }
  * { margin: 0; padding: 0; box-sizing: border-box; }
  html, body {
    width: 1200px;
    height: 1000px;
    overflow: hidden;
    background: var(--page);
  }
  .canvas {
    position: relative;
    width: 1200px;
    height: 1000px;
    overflow: hidden;
    color: var(--ink);
  }
  .masthead {
    position: absolute;
    left: 0;
    top: 140px;
    width: 1200px;
    text-align: center;
  }
  .masthead__name {
    font-family: "Lato", sans-serif;
    font-weight: 300;
    font-size: 82px;
    line-height: 1;
    letter-spacing: 0.2em;
    padding-left: 0.2em;
    white-space: nowrap;
  }
  .masthead__address {
    margin-top: 60px;
    font-family: "Crimson Text", serif;
    font-size: 25px;
    letter-spacing: 0.08em;
    white-space: nowrap;
  }
  .masthead__rule {
    width: 712px;
    height: 1px;
    margin: 26px auto 0;
    background: var(--accent-blue);
  }
  .sheet {
    position: absolute;
    left: 631px;
    top: 494px;
    width: 469px;
    height: 560px;
    background: var(--sheet);
    border: 1px solid var(--sheet-border);
    text-align: center;
  }
  .sheet__name {
    margin-top: 20px;
    font-family: "Lato", sans-serif;
    font-weight: 400;
    font-size: 21px;
    line-height: 1;
    letter-spacing: 0.16em;
    padding-left: 0.16em;
    white-space: nowrap;
  }
  .sheet__address {
    margin-top: 13px;
    font-family: "Crimson Text", serif;
    font-size: 7.5px;
    letter-spacing: 0.06em;
    white-space: nowrap;
  }
  .sheet__rule {
    width: 200px;
    height: 1px;
    margin: 5px auto 0;
    background: var(--accent-blue);
  }
</style>
</head>
<body>
  <main class="canvas">
    <header class="masthead">
      <h1 class="masthead__name">DOMINIC LEE HARLOW</h1>
      <p class="masthead__address">2750 Aperture Lane, Sausalito, California 94965</p>
      <div class="masthead__rule"></div>
    </header>

    <section class="sheet" aria-label="Letterhead sheet">
      <h2 class="sheet__name">DOMINIC LEE HARLOW</h2>
      <p class="sheet__address">2750 Aperture Lane, Sausalito, California 94965</p>
      <div class="sheet__rule"></div>
    </section>
  </main>
</body>
</html>
```